business card deign

Logo needs the following on it.
1. attached logo
2. Tagline - "If it keeps a drink cold or the party going...we do it!"
3. Name- Dalton Pikes, Founder and CPO
4. Address - 412 E. Carver Avenue, Ste 2207, Tampa, FL. 33917
5. Phone - 555.318.4726

```html
<!DOCTYPE html>
<html lang="en">
<head>
<meta charset="utf-8">
<title>KOOLHOP Business Card</title>
<link rel="stylesheet" href="https://fonts.googleapis.com/css2?family=Montserrat:wght@400;500;700&display=swap">
<style>
  :root {
    --page-bg: #e6e4e2;
    --card-bg: #ffffff;
    --ink: #111111;
    --ink-soft: #333333;
    --rule: #222222;
  }
  * { box-sizing: border-box; margin: 0; padding: 0; }
  html, body {
    width: 1200px; height: 786px; overflow: hidden;
    background: var(--page-bg);
    font-family: "Montserrat", Arial, sans-serif;
    color: var(--ink);
  }
  .stage {
    position: relative; width: 1200px; height: 786px;
  }
  .card {
    position: absolute; top: 238px;
    width: 540px; height: 310px;
    background: var(--card-bg);
    box-shadow: 0 6px 18px rgba(0,0,0,0.18);
  }
  .card--front { left: 40px; }
  .card--back { left: 620px; }

  /* Front */
  .brand {
    position: absolute; left: 42px; top: 150px;
    display: flex; align-items: center; gap: 12px;
  }
  .brand__dot {
    width: 18px; height: 18px; border-radius: 50%;
    background: var(--ink);
  }
  .brand__name {
    font-weight: 700; font-size: 26px; letter-spacing: 9px;
    color: var(--ink);
  }
  .divider {
    position: absolute; left: 268px; top: 52px;
    width: 1.5px; height: 170px; background: var(--rule);
  }
  .details {
    position: absolute; left: 286px; top: 46px;
    font-size: 12px; color: var(--ink-soft); line-height: 1.3;
  }
  .details__name { font-weight: 700; font-size: 17px; color: var(--ink); }
  .details__role { font-size: 11.5px; margin-bottom: 16px; }
  .details__address { margin-bottom: 12px; }
  .contact { list-style: none; }
  .contact li { display: flex; align-items: center; gap: 8px; margin-bottom: 7px; }
  .contact svg { width: 11px; height: 11px; flex: none; }
  .tagline {
    position: absolute; left: 0; right: 0; bottom: 34px;
    text-align: center; font-size: 13.5px; font-weight: 500; color: var(--ink);
  }

  /* Back */
  .back-mark {
    position: absolute; left: 70px; top: 70px;
    width: 170px; height: 170px; border-radius: 50%;
    background: var(--ink);
  }
  .back-name {
    position: absolute; right: 36px; top: 132px;
    font-weight: 700; font-size: 26px; letter-spacing: 9px;
    color: var(--ink);
  }
</style>
</head>
<body>
<main class="stage">
  <section class="card card--front">
    <div class="brand">
      <span class="brand__dot"></span>
      <span class="brand__name">KOOLHOP</span>
    </div>
    <div class="divider"></div>
    <div class="details">
      <p class="details__name">Dalton Pikes</p>
      <p class="details__role">Founder and CPO</p>
      <p class="details__address">412 E. Carver Avenue, Ste 2207,<br>Tampa, FL. 33917</p>
      <ul class="contact">
        <li>
          <svg viewBox="0 0 12 12"><path d="M2.5 1 L4.5 1 L5.2 3.4 L4 4.4 Q5 6.8 7.6 8 L8.6 6.8 L11 7.5 L11 9.5 Q10.5 11 9 11 Q1 10 1 2.5 Q1 1 2.5 1Z" fill="#111"/></svg>
          555.318.4726
        </li>
        <li>
          <svg viewBox="0 0 12 12"><rect x="0.5" y="2.5" width="11" height="7.5" fill="#111"/><path d="M0.5 2.5 L6 7 L11.5 2.5" stroke="#fff" stroke-width="1" fill="none"/></svg>
          info@koolhop.com
        </li>
        <li>
          <svg viewBox="0 0 12 12"><circle cx="6" cy="6" r="5.2" fill="#111"/><path d="M1 6 H11 M6 1 Q3 6 6 11 M6 1 Q9 6 6 11" stroke="#fff" stroke-width="0.8" fill="none"/></svg>
          www.koolhop.com
        </li>
      </ul>
    </div>
    <p class="tagline">If it keeps a drink cold or the party going...we do it</p>
  </section>

  <section class="card card--back">
    <div class="back-mark"></div>
    <span class="back-name">KOOLHOP</span>
  </section>
</main>
</body>
</html>
```